Internal web page of multinational company - Portfolio of reports

We need to improve the look & feel of an existing internal HTML page.
We use it as a portfolios where users go and see a list of existing reports as "tiles". The HTML page is automatically generated by a javascript that reads the contents to display from an HTML file.
What is needs is a "face lift" in the design of the page.
Currently we use icons on the top right of each tile to denote the type of technology used on the report and also colons for the same purpose. The attached screenshots will be self explanatory.
Across the top we have "tabs" that, once selected change the tiles.
Need a proposal for new design that keeps is as clean as possible, specially the home page that should be very light (Plimbo like).
The idea for this page is to serve as a "one stop shop" and become a bookmark for everyone in the company.
Looking for a wow effect that make is visually

Target Market(s)

Internal employees

Industry/Entity Type

It Company

Coding

Coded - Design and coding required

Number of Pages Required

2 page

Requirements
Must have
• Should not change the logo or its position from the bottom left.
• Page must be as clean as possible and
Nice to have
• Welcome to change the logo on the top left. This page is from the CSU M&I (Mni) which stands for Central Support Unit - Metrics & Insight.
Should not have
• Do no use red, this is the color of our competitor. The blue on the bottom is standard for our logo

```html
<!DOCTYPE html>
<html lang="en">
<head>
<meta charset="utf-8">
<title>CSU M&amp;I – Report Portfolio</title>
<link href="https://fonts.googleapis.com/css2?family=Roboto:wght@400;500;700&family=Roboto+Condensed:wght@700&display=swap" rel="stylesheet">
<style>
:root{
  --brand-blue:#0056a6;
  --brand-deep:#003f7f;
  --nav-active:#1b73d0;
  --tile-bg:#f3f3f3;
  --tile-rule:#c6c6c6;
  --text-blue:#1a6dc6;
  --text-orange:#f7941d;
  --text-green:#0c9d4a;
  --icon-grey:#a4a4a4;
  --footer-bg:#3a3a3a;
  --footer-dark:#2b2b2b;
  --footer-text:#bdbdbd;
  --white:#ffffff;
}
*{box-sizing:border-box;margin:0;padding:0}
html,body{width:1200px;height:804px;overflow:hidden;background:var(--white);font-family:"Roboto",Arial,sans-serif}
.page{position:relative;width:1200px;height:804px}

/* header */
.masthead{position:absolute;left:0;top:0;width:1200px;height:69px;background:var(--brand-blue);color:var(--white)}
.brand{position:absolute;left:99px;top:12px;font-family:"Roboto Condensed",Arial,sans-serif;font-weight:700;font-size:39px;letter-spacing:.5px;line-height:44px}
.section-switch{position:absolute;left:258px;top:0;width:93px;height:69px;background:var(--brand-deep);text-align:center;font-family:"Roboto Condensed",Arial,sans-serif;font-weight:700;font-size:13px;letter-spacing:.3px}
.section-switch svg{display:block;margin:11px auto 3px}
.section-switch .caret{display:block;margin:4px auto 0}
.main-nav{position:absolute;left:358px;top:0;height:69px;display:flex;list-style:none}
.main-nav li{height:69px;line-height:68px;padding:0 12px;font-size:12px}
.main-nav li.is-active{background:var(--nav-active);padding:0 12px}
.main-nav .filter{display:flex;align-items:center;gap:6px}
.search{position:absolute;left:907px;top:19px;width:193px;height:31px;background:var(--white);border-radius:2px;display:flex;align-items:center;padding:0 8px;color:#9a9a9a;font-size:11px;gap:6px}
.search .glass{margin-left:auto}

/* tiles */
.portfolio{position:absolute;left:99px;top:120px;display:grid;grid-template-columns:repeat(4,238px);grid-auto-rows:115px;column-gap:16.5px;row-gap:35px}
.tile{position:relative;background:var(--tile-bg);border-bottom:3px solid var(--tile-rule);color:var(--text-blue)}
.tile.is-orange{color:var(--text-orange)}
.tile.is-green{color:var(--text-green)}
.tile-meta{position:absolute;left:11px;top:14px;display:flex;align-items:center;gap:9px}
.tech{width:13px;height:13px;border-radius:3px}
.tech.kind-a{background:linear-gradient(135deg,#7dbb42,#f39c3c 50%,#3b8fd8)}
.tech.kind-b{background:#f0b04a}
.tech.kind-c{background:linear-gradient(135deg,#e8a33a,#4a7fc1)}
.dot{width:10px;height:10px;border-radius:50%;background:currentColor}
.close{width:9px;height:9px}
.tile-title{position:absolute;left:11px;top:37px;font-size:14.5px;font-weight:400;letter-spacing:.1px}
.tile-actions{position:absolute;left:11px;top:81px;display:flex;gap:14px;color:var(--icon-grey)}
.tile.is-hovered{border-bottom:none;height:115px}
.tile.is-hovered .tile-actions{left:0;right:0;top:78px;height:37px;background:var(--text-orange);color:var(--white);padding:10px 11px;align-items:flex-start}

/* tooltip */
.tooltip{position:absolute;left:209px;top:682px;width:268px;height:76px;background:var(--white);border:1px solid #d6d6d6;border-radius:2px;padding:12px 12px 0;z-index:3}
.tooltip::before{content:"";position:absolute;left:18px;top:-13px;border:12px solid transparent;border-top:none;border-bottom-color:var(--white);border-width:0 13px 13px}
.tooltip h3{font-size:12px;font-weight:400;color:#222;letter-spacing:.2px;margin-bottom:6px}
.tooltip p{font-size:11px;line-height:17px;color:#555}

/* footer */
.site-footer{position:absolute;left:0;top:735px;width:1200px;height:69px;background:var(--footer-bg)}
.help{position:absolute;left:98px;top:0;width:194px;height:69px;background:var(--footer-dark);color:#cfcfcf;display:flex;align-items:center;gap:10px;padding-left:22px;font-weight:700;font-size:13.5px;letter-spacing:.3px}
.copyright{position:absolute;right:100px;top:28px;color:var(--footer-text);font-size:10.5px}
.rev{position:absolute;right:6px;bottom:5px;color:#9a9a9a;font-size:10px}
</style>
</head>
<body>
<svg width="0" height="0" style="position:absolute" aria-hidden="true">
  <symbol id="i-wrench" viewBox="0 0 16 16"><path fill="currentColor" d="M14.6 3.4l-2.3 2.3-2-.6-.6-2L12 .8A4.3 4.3 0 006.6 6.3L.8 12.1a1.6 1.6 0 002.3 2.3l5.8-5.8a4.3 4.3 0 005.7-5.2z"/></symbol>
  <symbol id="i-doc" viewBox="0 0 16 16"><path fill="none" stroke="currentColor" stroke-width="1.3" d="M3 1h7l3 3v11H3z M5.5 7h5 M5.5 9.5h5 M5.5 12h5"/></symbol>
  <symbol id="i-chart" viewBox="0 0 18 16"><path fill="currentColor" d="M1 2h1.3v12H17v1.3H1z M4 8h1.6v5H4z M7 5h1.6v8H7z M10 9h1.6v4H10z M13 4h1.6v9H13z"/></symbol>
  <symbol id="i-x" viewBox="0 0 10 10"><path stroke="#9b9b9b" stroke-width="2.2" d="M1.5 1.5l7 7M8.5 1.5l-7 7"/></symbol>
</svg>

<div class="page">
  <header class="masthead">
    <div class="brand">CSU M&amp;I</div>
    <div class="section-switch">
      <svg width="20" height="14" viewBox="0 0 20 14"><rect x="1" y="1" width="18" height="12" rx="1.5" fill="none" stroke="#fff" stroke-width="2"/><circle cx="10" cy="7" r="3" fill="#fff"/></svg>
      FINANCE
      <svg class="caret" width="10" height="6" viewBox="0 0 10 6"><path d="M0 0h10L5 6z" fill="#fff"/></svg>
    </div>
    <ul class="main-nav">
      <li>GM View</li><li>Hub View</li><li>MI</li>
      <li class="is-active">General Accounting</li>
      <li>Tzx</li><li>Treasury</li><li>Knowledge</li>
      <li class="filter">Filter <svg width="9" height="5" viewBox="0 0 9 5"><path d="M0 0h9L4.5 5z" fill="#fff"/></svg></li>
    </ul>
    <div class="search">
      <svg width="11" height="11"><use href="#i-x"/></svg>Search
      <svg class="glass" width="17" height="17" viewBox="0 0 17 17"><circle cx="7" cy="7" r="5.5" fill="none" stroke="#666" stroke-width="2.2"/><path d="M11 11l5 5" stroke="#666" stroke-width="2.6"/></svg>
    </div>
  </header>

  <main class="portfolio">
    <article class="tile"><div class="tile-meta"><span class="tech kind-a"></span><span class="dot"></span><svg class="close"><use href="#i-x"/></svg></div><h2 class="tile-title">B&amp;AT Revenue &amp; Margin Analysis</h2><div class="tile-actions"><svg width="14" height="14"><use href="#i-wrench"/></svg><svg width="14" height="14"><use href="#i-doc"/></svg><svg width="17" height="14"><use href="#i-chart"/></svg></div></article>
    <article class="tile is-orange"><div class="tile-meta"><span class="tech kind-b"></span><span class="dot"></span><svg class="close"><use href="#i-x"/></svg></div><h2 class="tile-title">B&amp;AT Revenue &amp; Margin Analysis</h2><div class="tile-actions"><svg width="14" height="14"><use href="#i-wrench"/></svg><svg width="14" height="14"><use href="#i-doc"/></svg><svg width="17" height="14"><use href="#i-chart"/></svg></div></article>
    <article class="tile"><div class="tile-meta"><span class="tech kind-a"></span><span class="dot"></span><svg class="close"><use href="#i-x"/></svg></div><h2 class="tile-title">B&amp;AT Revenue &amp; Margin Analysis</h2><div class="tile-actions"><svg width="14" height="14"><use href="#i-wrench"/></svg><svg width="14" height="14"><use href="#i-doc"/></svg><svg width="17" height="14"><use href="#i-chart"/></svg></div></article>
    <article class="tile"><div class="tile-meta"><span class="tech kind-a"></span><span class="dot"></span><svg class="close"><use href="#i-x"/></svg></div><h2 class="tile-title">B&amp;AT Revenue &amp; Margin Analysis</h2><div class="tile-actions"><svg width="14" height="14"><use href="#i-wrench"/></svg><svg width="14" height="14"><use href="#i-doc"/></svg><svg width="17" height="14"><use href="#i-chart"/></svg></div></article>

    <article class="tile"><div class="tile-meta"><span class="tech kind-a"></span><span class="dot"></span><svg class="close"><use href="#i-x"/></svg></div><h2 class="tile-title">B&amp;AT Revenue &amp; Margin Analysis</h2><div class="tile-actions"><svg width="14" height="14"><use href="#i-wrench"/></svg><svg width="14" height="14"><use href="#i-doc"/></svg><svg width="17" height="14"><use href="#i-chart"/></svg></div></article>
    <article class="tile"><div class="tile-meta"><span class="tech kind-a"></span><span class="dot"></span><svg class="close"><use href="#i-x"/></svg></div><h2 class="tile-title">B&amp;AT Revenue &amp; Margin Analysis</h2><div class="tile-actions"><svg width="14" height="14"><use href="#i-wrench"/></svg><svg width="14" height="14"><use href="#i-doc"/></svg><svg width="17" height="14"><use href="#i-chart"/></svg></div></article>
    <article class="tile"><div class="tile-meta"><span class="tech kind-a"></span><span class="dot"></span><svg class="close"><use href="#i-x"/></svg></div><h2 class="tile-title">B&amp;AT Revenue &amp; Margin Analysis</h2><div class="tile-actions"><svg width="14" height="14"><use href="#i-wrench"/></svg><svg width="14" height="14"><use href="#i-doc"/></svg><svg width="17" height="14"><use href="#i-chart"/></svg></div></article>
    <article class="tile"><div class="tile-meta"><span class="tech kind-a"></span><span class="dot"></span><svg class="close"><use href="#i-x"/></svg></div><h2 class="tile-title">B&amp;AT Revenue &amp; Margin Analysis</h2><div class="tile-actions"><svg width="14" height="14"><use href="#i-wrench"/></svg><svg width="14" height="14"><use href="#i-doc"/></svg><svg width="17" height="14"><use href="#i-chart"/></svg></div></article>

    <article class="tile"><div class="tile-meta"><span class="tech kind-b"></span><span class="dot"></span><svg class="close"><use href="#i-x"/></svg></div><h2 class="tile-title">B&amp;AT Revenue &amp; Margin Analysis</h2><div class="tile-actions"><svg width="14" height="14"><use href="#i-wrench"/></svg><svg width="14" height="14"><use href="#i-doc"/></svg><svg width="17" height="14"><use href="#i-chart"/></svg></div></article>
    <article class="tile"><div class="tile-meta"><span class="tech kind-a"></span><span class="dot"></span><svg class="close"><use href="#i-x"/></svg></div><h2 class="tile-title">B&amp;AT Revenue &amp; Margin Analysis</h2><div class="tile-actions"><svg width="14" height="14"><use href="#i-wrench"/></svg><svg width="14" height="14"><use href="#i-doc"/></svg><svg width="17" height="14"><use href="#i-chart"/></svg></div></article>
    <article class="tile is-orange"><div class="tile-meta"><span class="tech kind-a"></span><span class="dot"></span><svg class="close"><use href="#i-x"/></svg></div><h2 class="tile-title">B&amp;AT Revenue &amp; Margin Analysis</h2><div class="tile-actions"><svg width="14" height="14"><use href="#i-wrench"/></svg><svg width="14" height="14"><use href="#i-doc"/></svg><svg width="17" height="14"><use href="#i-chart"/></svg></div></article>
    <article class="tile is-green"><div class="tile-meta"><span class="tech kind-c"></span><span class="dot"></span><svg class="close"><use href="#i-x"/></svg></div><h2 class="tile-title">B&amp;AT Revenue &amp; Margin Analysis</h2><div class="tile-actions"><svg width="14" height="14"><use href="#i-wrench"/></svg><svg width="14" height="14"><use href="#i-doc"/></svg><svg width="17" height="14"><use href="#i-chart"/></svg></div></article>

    <article class="tile is-orange is-hovered"><div class="tile-meta"><span class="tech kind-b"></span><span class="dot"></span><svg class="close"><use href="#i-x"/></svg></div><h2 class="tile-title">B&amp;AT Revenue &amp; Margin Analysis</h2><div class="tile-actions"><svg width="14" height="14"><use href="#i-wrench"/></svg><svg width="14" height="14"><use href="#i-doc"/></svg><svg width="17" height="14"><use href="#i-chart"/></svg></div></article>
    <article class="tile"><div class="tile-meta"><span class="tech kind-a"></span><span class="dot"></span><svg class="close"><use href="#i-x"/></svg></div><h2 class="tile-title">B&amp;AT Revenue &amp; Margin Analysis</h2><div class="tile-actions"><svg width="14" height="14"><use href="#i-wrench"/></svg><svg width="14" height="14"><use href="#i-doc"/></svg><svg width="17" height="14"><use href="#i-chart"/></svg></div></article>
  </main>

  <aside class="tooltip">
    <h3>STATEMENT OF RECHARGE ONLINE TOOL</h3>
    <p>- This tool is used for approval of intercompany recharges. Scope : Globe</p>
  </aside>

  <footer class="site-footer">
    <div class="help">
      <svg width="28" height="24" viewBox="0 0 28 24"><path d="M14 2C7.4 2 2 5.9 2 10.7c0 2.6 1.6 4.9 4.1 6.5L4.5 22l5.8-3c1.2.3 2.4.4 3.7.4 6.6 0 12-3.9 12-8.7S20.6 2 14 2z" fill="none" stroke="#cfcfcf" stroke-width="2"/></svg>
      HELP &amp; FEEDBACK
    </div>
    <p class="copyright">Copyright &copy; 2015 CSU-M&amp;I. &nbsp;All rights reserved.</p>
    <span class="rev">M2</span>
  </footer>
</div>
</body>
</html>
```